Computer Training in the Education sector - Letterhead

We need a new letter head to be designed for the company. We provide computer training fro the Education Sector, both primary and private tertiary providers. The colours will need to tie in with the website www.crossingthestream.co.nz.
The company name is Crossing the Stream with the tag line of Computer Training for Educators.
The footer will need to have the following detail...
0508 PCS MENTOR
021 839 415
www.crossingthestream.co.nz / training@crossingthestream.co.nz
Updates

Thanks for the designs so far.

Some have watermarks in the background. Please don't worry about using watermarks as I will not be using a watermark in in a final design.
Regards,
Roger

Thank you for all the designs and the effort. There was some great concepts that came through.

Cheers
Roger

Industry/Entity Type

Computer

```html
<!DOCTYPE html>
<html lang="en">
<head>
<meta charset="utf-8">
<title>Crossing the Stream — Letterhead</title>
<link rel="stylesheet" href="https://fonts.googleapis.com/css2?family=Arimo:wght@400;700&display=swap">
<style>
  :root {
    --paper: #ffffff;
    --ink: #1f1f1f;
    --brand-blue: #2f6fb6;
    --brand-orange: #e4822f;
    --rule: #9a9a9a;
  }
  html, body {
    margin: 0;
    padding: 0;
    width: 1036px;
    height: 1200px;
    overflow: hidden;
    background: var(--paper);
  }
  .letterhead {
    position: relative;
    width: 1036px;
    height: 1200px;
    background: var(--paper);
    font-family: "Arimo", Arial, sans-serif;
    color: var(--ink);
  }
  .brand {
    position: absolute;
    left: 80px;
    top: 42px;
    display: flex;
    align-items: center;
    gap: 12px;
  }
  .brand-dot {
    width: 14px;
    height: 14px;
    border-radius: 50%;
    background: var(--brand-orange);
    flex: none;
  }
  .brand-name {
    margin: 0;
    font-size: 27px;
    font-weight: 700;
    line-height: 1.1;
    color: var(--brand-blue);
    width: 150px;
  }
  .tagline {
    position: absolute;
    left: 255px;
    top: 94px;
    margin: 0;
    font-size: 18px;
    font-weight: 700;
    letter-spacing: 1.2px;
    color: var(--ink);
  }
  .contact {
    position: absolute;
    left: 710px;
    top: 52px;
    margin: 0;
    padding: 2px 0 2px 17px;
    border-left: 1px solid var(--rule);
    list-style: none;
    font-size: 15px;
    line-height: 25.5px;
    color: var(--ink);
  }
</style>
</head>
<body>
  <main class="letterhead">
    <header>
      <div class="brand">
        <span class="brand-dot" aria-hidden="true"></span>
        <h1 class="brand-name">Crossing the Stream</h1>
      </div>
      <p class="tagline">Computer Training for Educators</p>
      <ul class="contact">
        <li>P: 0508 PCS MENTOR</li>
        <li>F: 021 839 415</li>
        <li>E: training@crossingthestream.co.nz</li>
        <li>W: www.crossingthestream.co.nz</li>
      </ul>
    </header>
  </main>
</body>
</html>
```